Wandering Rooms Stationary Set

Wandering Rooms is a bespoke interior design firm set to provide services to VIP clients with elegance and minimalism is the main theme for our stationary set. We require a full stationary set covering A4 letterhead, A4 & A3 envelopes, business cards, USB's, CDs, email signature and any other item the designer sees fit. logo is already designed and finalized, and we require the designer to use it as is without modifying the logo.

Address to be used on letterhead / business cards ...etc shall be as follows:

Phone : +971 2 518 2047
P.O. Box : 309186
Address: Block C&D, Bldg. 47, Court 12, Abu Dhabi, United Arab Emirates
Website: www.wanderingrooms-example.com

Target Market(s)

VIP Clients

Industry/Entity Type

Interior Design

Font styles to use
Other font styles liked:
• something to be unique

Colors

Designer to choose colors to be used in the design.

Requirements
Must have
• Elegant, minimalistic
Nice to have
• Simple yet elegant design having a sharp yet clean cut format
Should not have
• No additional colours, just colours that are used in the logo (silver, black or gold)

```html
<!DOCTYPE html>
<html lang="en">
<head>
<meta charset="utf-8">
<title>Wandering Rooms – Business Card</title>
<link rel="stylesheet" href="https://fonts.googleapis.com/css2?family=EB+Garamond:wght@400;500&family=Allura&display=swap">
<style>
  :root {
    --backdrop: #1c1c1c;
    --card: #262626;
    --gold: #b9954f;
    --silver: #a9a9a9;
    --silver-soft: #8a8a8a;
    --ink: #1e1e1e;
  }
  * { margin: 0; padding: 0; box-sizing: border-box; }
  html, body {
    width: 1200px; height: 800px; overflow: hidden;
    background: var(--backdrop);
    font-family: "EB Garamond", Georgia, serif;
  }
  .sheet {
    position: relative; width: 1200px; height: 800px;
  }
  .card {
    position: absolute; left: 320px;
    width: 560px; height: 320px;
    background: var(--card);
    box-shadow: 0 10px 30px rgba(0,0,0,.5);
    overflow: hidden;
  }
  .card--front { top: 50px; }
  .card--back { top: 420px; }

  /* Front */
  .card--front .brand {
    position: absolute; inset: 0;
    display: flex; align-items: center; justify-content: center; gap: 14px;
    color: var(--silver);
    font-size: 40px; font-weight: 400; letter-spacing: 4px;
  }
  .brand-dot {
    width: 12px; height: 12px; border-radius: 50%;
    background: currentColor;
  }

  /* Back */
  .card--back .brand {
    position: absolute; left: 40px; top: 70px;
    color: var(--gold);
    font-size: 32px; font-weight: 400; letter-spacing: 3px;
  }
  .holder {
    position: absolute; right: 40px; top: 34px; text-align: right;
  }
  .holder-name {
    font-family: "Allura", cursive;
    color: var(--gold); font-size: 34px; line-height: 1;
  }
  .holder-title {
    color: var(--silver); font-size: 15px; margin-top: 2px;
  }
  .contact {
    position: absolute; right: 40px; bottom: 70px;
    text-align: right; color: var(--silver-soft);
    font-size: 12.5px; line-height: 1.45;
  }
  .contact b { color: var(--gold); font-weight: 500; }
  .address {
    position: absolute; left: 40px; bottom: 70px;
    color: var(--silver-soft); font-size: 12.5px; line-height: 1.45;
  }
  .web-band {
    position: absolute; left: 0; right: 0; bottom: 24px; height: 30px;
    background: var(--gold);
    display: flex; align-items: center; padding-left: 40px;
    color: var(--ink); font-size: 13px; letter-spacing: 2px;
  }
</style>
</head>
<body>
<main class="sheet">
  <section class="card card--front" aria-label="Business card front">
    <div class="brand"><span class="brand-dot"></span>Wandering Rooms</div>
  </section>

  <section class="card card--back" aria-label="Business card back">
    <div class="brand">Wandering Rooms</div>
    <div class="holder">
      <div class="holder-name">Daniel Hart</div>
      <div class="holder-title">President</div>
    </div>
    <div class="address">
      P.O. Box : 309186<br>
      Block C&amp;D, Bldg. 47, Court 12<br>
      Abu Dhabi, United Arab Emirates
    </div>
    <div class="contact">
      <b>P :</b> +971 2 518 2047<br>
      <b>E :</b> info@wanderingrooms-example.com
    </div>
    <div class="web-band">www.wanderingrooms-example.com</div>
  </section>
</main>
</body>
</html>
```